Electrician Letterhead Design MVR

We need some letterhead for our bills and other papers.
Customer address is on the right side (Swiss format)
A4 format

Design should also be applicable on Cards

Target Market(s)

Private Customers, Small Business

Industry/Entity Type

Electrician

Other font styles liked:
• incised 901

Colors
00AB8E
00BBA5
67D7C9
C6EFE9
E9F9F6

```html
<!DOCTYPE html>
<html lang="de">
<head>
<meta charset="utf-8">
<title>MVR Letterhead</title>
<link href="https://fonts.googleapis.com/css2?family=Exo+2:wght@500;700&family=Open+Sans:wght@400&display=swap" rel="stylesheet">
<style>
  :root {
    --teal-dark: #00AB8E;
    --teal: #00BBA5;
    --teal-light: #67D7C9;
    --teal-pale: #C6EFE9;
    --teal-mist: #E9F9F6;
    --paper: #f4f5f5;
    --backdrop: #dcdcdc;
    --ink: #1f2a28;
    --white: #ffffff;
  }
  * { margin: 0; padding: 0; box-sizing: border-box; }
  html, body {
    width: 1200px; height: 800px; overflow: hidden;
    background: var(--backdrop);
  }
  .sheet {
    position: absolute;
    left: 338px; top: 30px;
    width: 524px; height: 740px;
    background: var(--paper);
    box-shadow: 0 2px 10px rgba(0,0,0,0.12);
    overflow: hidden;
  }
  .header-band {
    position: absolute; left: 0; top: 0;
    width: 524px; height: 140px;
  }
  .contact {
    position: absolute; right: 24px; top: 14px;
    width: 180px;
    font-family: "Open Sans", sans-serif;
    font-style: normal;
    font-size: 8px; line-height: 1.3;
    color: var(--white);
  }
  .contact-address { margin-bottom: 2px; }
  .contact-list { list-style: none; }
  .contact-list li { display: flex; align-items: center; gap: 6px; }
  .contact-list li::before {
    content: ""; width: 6px; height: 6px; border-radius: 50%;
    background: var(--teal-pale); flex: none;
  }
  .brand {
    position: absolute; left: 32px; top: 110px;
    font-family: "Exo 2", sans-serif;
  }
  .brand-name {
    display: flex; align-items: center; gap: 6px;
    font-size: 40px; font-weight: 700; line-height: 1;
    color: var(--teal-dark); letter-spacing: 1px;
  }
  .brand-dot {
    width: 10px; height: 10px; border-radius: 50%;
    background: var(--teal-dark);
  }
  .brand-tagline {
    margin-top: 2px;
    font-size: 9.5px; font-weight: 500; color: var(--ink);
    letter-spacing: 0.2px;
  }
  .sheet-mark {
    position: absolute; left: 150px; top: 330px;
    font-family: "Exo 2", sans-serif;
    font-size: 150px; font-weight: 700;
    color: var(--teal-mist); opacity: 0.7;
    line-height: 1;
  }
</style>
</head>
<body>
  <main class="sheet">
    <svg class="header-band" viewBox="0 0 524 140" aria-hidden="true">
      <path d="M145,0 H524 V104 C480,118 430,130 370,124 C308,118 258,72 145,66 Z" fill="var(--teal-pale)"/>
      <path d="M160,0 H524 V96 C480,110 430,122 372,116 C310,110 260,66 160,60 Z" fill="var(--teal-dark)"/>
      <path d="M145,66 C258,72 308,118 370,124 C430,130 480,118 524,104" fill="none" stroke="var(--teal)" stroke-width="1.5"/>
    </svg>

    <address class="contact">
      <p class="contact-address">Suite 102 Street name,<br>State, Zip 2034, Country</p>
      <ul class="contact-list">
        <li>+01-1234-567890</li>
        <li>+01-1234-567891</li>
        <li>info@morvanelektro.com</li>
        <li>www.morvanelektro.com</li>
      </ul>
    </address>

    <header class="brand">
      <div class="brand-name">MVR <span class="brand-dot"></span></div>
      <div class="brand-tagline">Elektrotechnik Morvan GmbH</div>
    </header>

    <div class="sheet-mark" aria-hidden="true">MVR</div>
  </main>
</body>
</html>
```